Facebook template for supermarket

I need a new fresh Facebook template in which I can paste an image that changes depending on the content of the Facebook post. I need to be able to change the design in Adobe Photoshop. It concerns the FB page of a local supermarket.
I once made a template myself, but I'm not satisfied with it.
Check the supermarket's website to see the supermarket's color scheme and style. The supermarket is a forerunner in the field of fresh products from local suppliers and has a wide range of organic products.
The slogan of the supermarket is 'With VELDO you find fine meals, your street and true friends'. The supermarket has a strong bond with the neighborhood and the inhabitants.
I have added my self-made template as an example. At the bottom right is the name of the owners of the supermarket.

```html
<!DOCTYPE html>
<html lang="en">
<head>
<meta charset="utf-8">
<title>VELDO Facebook post template</title>
<link rel="stylesheet" href="https://fonts.googleapis.com/css2?family=Montserrat:wght@400;700;800&display=swap">
<style>
  :root {
    --frame: #e4ecdc;
    --green: #66bb2a;
    --green-dark: #4f9a1c;
    --ink: #3d4a3a;
    --white: #ffffff;
    --photo-a: #3d4a3a;
    --photo-b: #2f7a3a;
    --photo-c: #c9735a;
  }
  * { margin: 0; padding: 0; box-sizing: border-box; }
  html, body { width: 1200px; height: 1200px; overflow: hidden; background: var(--frame); }
  body { font-family: "Montserrat", sans-serif; }
  .post {
    position: relative;
    width: 1200px;
    height: 1200px;
    background: var(--frame);
  }
  .post-area {
    position: absolute;
    left: 15px; top: 15px;
    width: 1170px; height: 1170px;
    background: var(--green);
    overflow: hidden;
  }
  .photo-slot {
    position: absolute;
    left: 0; top: 200px;
    width: 1170px; height: 820px;
    background:
      radial-gradient(ellipse at 40% 65%, rgba(214,130,100,0.85) 0%, rgba(214,130,100,0) 55%),
      radial-gradient(ellipse at 85% 70%, rgba(200,110,80,0.7) 0%, rgba(200,110,80,0) 45%),
      linear-gradient(180deg, var(--photo-a) 0%, #5a5248 35%, var(--photo-b) 60%, var(--photo-c) 100%);
  }
  .shapes { position: absolute; left: 0; top: 0; width: 1170px; height: 1170px; }
  .headline {
    position: absolute;
    left: 0; top: 52px;
    width: 1170px;
    text-align: center;
    color: var(--white);
    font-weight: 800;
    font-size: 45px;
    line-height: 58px;
  }
  .slogan {
    position: absolute;
    left: 48px; top: 1045px;
    width: 560px;
    color: var(--white);
    font-size: 27px;
    line-height: 44px;
    font-weight: 400;
  }
  .slogan strong { font-weight: 800; }
  .store-block {
    position: absolute;
    left: 740px; top: 1030px;
    width: 400px;
    text-align: center;
  }
  .store-name {
    color: var(--ink);
    font-weight: 700;
    font-size: 44px;
    line-height: 52px;
    letter-spacing: 2px;
  }
  .owners {
    margin-top: 10px;
    color: var(--ink);
    font-weight: 700;
    font-size: 23px;
    line-height: 28px;
  }
</style>
</head>
<body>
  <div class="post">
    <div class="post-area">
      <div class="photo-slot" role="img" aria-label="Supermarket produce display with green crates of bagged apples and price signs"></div>
      <svg class="shapes" viewBox="0 0 1170 1170" aria-hidden="true">
        <path d="M0 0 H1170 V280 Q585 140 0 280 Z" fill="var(--green)"/>
        <path d="M0 280 Q585 140 1170 280" fill="none" stroke="var(--green-dark)" stroke-width="5"/>
        <rect x="0" y="1000" width="1170" height="170" fill="var(--green)"/>
        <polygon points="570,1170 750,922 1170,922 1170,1170" fill="var(--white)"/>
      </svg>
      <h1 class="headline">Lorem ipsum dolor nibh diam sit amet<br>consectetur adipiscing elit</h1>
      <p class="slogan">With <strong>VELDO</strong> you find <strong>fine meals</strong>,<br>your street and true friends</p>
      <div class="store-block">
        <p class="store-name">VELDO</p>
        <p class="owners">Mark en Lotte de Vries</p>
      </div>
    </div>
  </div>
</body>
</html>
```